Direct to Consumer extended service contract business with a new disruptive business model needs a

We need a customized wordpress design for a company called 'Bright Harbor Assurance'.
We provide an innovative and unique service contract protection program direct to consumers. This program provides monthly coverage for all electronics purchased in the last 4 years and all electronics the consumer purchases in the future for a low monthly fee. The overall design should communicate a sense of legitimacy, ethics, and superior customer service and support (in an industry that has a huge PR issue to overcome).
Electronics is the first product group, other product groups with different price points to launch in the future..

Target Market(s)

All purchasers of electronic goods...all demographics

Industry/Entity Type

Electronics

Font styles to use
Sans Serif

Requirements
Must have
• Customer Testimonials
Industry News
Customer ratings
Blog posts
Call to action messaging
Like the functional elements and design of quillmesa.example (need to be better)
Nice to have
• Like to see video testimonials
Social network "whats trending related to electronics or service contract industry"
Easy way to register products for warranty

```html
<!DOCTYPE html>
<html lang="en">
<head>
<meta charset="utf-8">
<title>Bright Harbor Assurance</title>
<link href="https://fonts.googleapis.com/css2?family=PT+Sans:ital,wght@0,400;0,700;1,400;1,700&family=Roboto+Condensed:ital,wght@0,700;1,700&display=swap" rel="stylesheet">
<style>
:root{
  --brown-dark:#3a2d23;
  --brown-band:#3b2f25;
  --beige:#d5c8b3;
  --orange:#cf4a0e;
  --orange-bright:#e9560f;
  --white:#ffffff;
  --ink:#1a1a1a;
  --muted:#8a8a8a;
  --rule:#c9c9c9;
  --star-red:#e0322a;
  --star-blue:#2f86e0;
  --star-green:#7cc42a;
}
*{box-sizing:border-box;margin:0;padding:0}
html,body{width:1200px;height:2748px;overflow:hidden}
body{position:relative;background:var(--white);font-family:"PT Sans",sans-serif;color:var(--ink)}
.abs{position:absolute}

/* header */
.site-header{position:absolute;left:0;top:0;width:1200px;height:119px;background:var(--brown-dark)}
.brand{position:absolute;left:96px;top:28px;display:flex;align-items:center;gap:14px}
.brand-mark{width:56px;height:56px;border-radius:50%;background:#c9a86a}
.brand-name{font-family:"PT Sans",sans-serif;font-weight:700;font-size:26px;line-height:30px;color:#f1e7d3;width:210px}
.utility-bar{position:absolute;left:916px;top:0;width:262px;height:33px;background:var(--orange);display:flex;justify-content:space-around;align-items:center;font:700 15px "PT Sans",sans-serif;color:var(--white)}
.main-nav{position:absolute;right:30px;top:62px;display:flex;gap:28px;font:700 19px "PT Sans",sans-serif;color:#e8dcc8;letter-spacing:.5px}
.main-nav .active{color:#f4d27a;border-bottom:2px solid #f4d27a;padding-bottom:3px}

/* hero */
.hero{position:absolute;left:0;top:119px;width:1200px;height:531px;background:var(--beige)}
.hero-device{position:absolute;left:55px;top:55px;width:559px;height:348px;border-radius:10px;background:linear-gradient(180deg,#e9e9e9,#b9bcc0)}
.hero-lines{position:absolute;left:641px;top:116px;display:flex;flex-direction:column;align-items:flex-end;gap:8px}
.hero-lines span{background:#1e1a16;color:var(--white);font:700 38px "PT Sans",sans-serif;letter-spacing:1.5px;padding:0 10px;line-height:44px}
.hero-cta{position:absolute;left:663px;top:282px;width:445px;height:57px;background:var(--orange-bright);color:var(--white);font:700 38px "PT Sans",sans-serif;text-align:center;line-height:57px}

/* features */
.features{position:absolute;left:101px;top:568px;width:998px;height:165px;background:var(--white)}
.feature{position:absolute;top:15px;width:319px}
.feature-head{height:73px;background:var(--orange);display:flex;align-items:center;gap:12px;padding-left:14px;color:var(--white);font:700 23px/24px "PT Sans",sans-serif;text-transform:uppercase}
.feature-head svg{flex:none}
.feature ul{list-style:none;margin-top:10px;padding-left:4px;font-size:15.5px;line-height:20px;color:#333}

/* ratings */
.band{position:absolute;left:0;width:1200px;background:var(--brown-band)}
.section-title{position:absolute;left:0;width:1200px;text-align:center;font:italic 700 33px "Roboto Condensed",sans-serif}
.band .section-title{color:var(--white)}
.light-title{color:var(--orange)}
.arrow{position:absolute}
.rating{position:absolute;top:112px;display:flex;gap:14px;align-items:flex-start}
.rating-icon{width:96px;height:96px;border-radius:50%}
.rating-name{font:700 29px "PT Sans",sans-serif;color:var(--white);line-height:32px}
.rating-desc{font:700 19px/24px "PT Sans",sans-serif;color:var(--white);width:200px}
.stars{margin-top:6px;display:flex;gap:6px}

/* cards */
.card{position:absolute;width:318px}
.card-img{width:318px;height:236px}
.card-title{font:400 24px "PT Sans",sans-serif;margin-top:6px;padding-left:6px}
.card-meta{font:italic 700 13px "PT Sans",sans-serif;color:var(--orange);padding-left:6px}
.card-rule{border:0;border-top:1px solid var(--rule);margin:22px 0 10px 6px}
.card-text{font:italic 13.5px/21px "PT Sans",sans-serif;color:var(--muted);padding-left:6px}
.blog-meta{font:italic 12px "PT Sans",sans-serif;color:var(--orange);padding-left:6px}

.video{position:absolute;top:106px;width:337px;height:187px;border:2px solid #6b6b6b;background:linear-gradient(90deg,#123a6b,#1c4f8a)}
.play{position:absolute;left:139px;top:64px}

/* footer */
.site-footer{position:absolute;left:0;top:2469px;width:1200px;height:242px;background:var(--brown-dark);color:var(--white)}
.footer-heading{position:absolute;top:40px;font:700 20px "Roboto Condensed",sans-serif;border-bottom:2px solid #e8e0d2;padding-bottom:6px}
.footer-links{position:absolute;top:84px;display:grid;grid-template-columns:130px 110px;font:700 16px/21px "PT Sans",sans-serif}
.social-squares{position:absolute;left:600px;top:18px;display:flex;gap:4px}
.social-squares span{width:38px;height:38px;border-radius:4px;background:#3a6bb5}
.feed{position:absolute;left:424px;top:78px;width:308px;height:154px;background:var(--white);padding:10px 14px}
.feed-item{display:flex;gap:10px;align-items:center;height:46px}
.feed-dot{width:36px;height:36px;border-radius:50%;background:var(--orange);flex:none}
.feed-name{font:10px "PT Sans",sans-serif;color:var(--orange);text-transform:uppercase}
.feed-text{font:10px "PT Sans",sans-serif;color:#222}
.contact{position:absolute;left:830px;top:84px;font:italic 700 15px/21px "PT Sans",sans-serif}
.contact div{display:flex;gap:8px;align-items:center}
.copyright{position:absolute;left:0;top:2711px;width:1200px;height:37px;background:#22190f;color:var(--white);text-align:center;font:700 14px/37px "PT Sans",sans-serif}
</style>
</head>
<body>

<header class="site-header">
  <div class="brand"><span class="brand-mark"></span><span class="brand-name">Bright Harbor Assurance</span></div>
  <div class="utility-bar"><span>Login</span><span>Support</span><span>Call: 555-014-2290</span></div>
  <nav class="main-nav"><span class="active">HOME</span><span>PLANS</span><span>BENEFITS</span><span>ABOUT US</span><span>BLOG</span><span>NEWS</span><span>CONTACT</span></nav>
</header>

<section class="hero">
  <div class="hero-device" role="img" aria-label="Laptop showing the quote form and customer rating panel"></div>
  <div class="hero-lines"><span>BUYS YOUR DEVICE</span><span>PAY MONTHLY TO SECURE</span><span>CLAIM/FIX YOUR DEVICE</span></div>
  <div class="hero-cta">GET FREE QUOTE</div>
</section>

<section class="features">
  <div class="feature" style="left:13px">
    <div class="feature-head"><svg width="46" height="40" viewBox="0 0 46 40"><rect x="3" y="10" width="40" height="22" rx="11" fill="#fff"/></svg>Purchase in low rates</div>
    <ul><li>- 1000 products available online</li><li>- Low as price as compare to market price</li><li>- Easy to purchase any product</li></ul>
  </div>
  <div class="feature" style="left:339px">
    <div class="feature-head"><svg width="44" height="50" viewBox="0 0 44 50"><path d="M4 4h36v20c0 12-9 20-18 24C13 44 4 36 4 24z" fill="#fff"/></svg>Protect devices by paying monthy</div>
    <ul><li>- Pay montly fee</li><li>- Low rates as compate to others</li><li>- Secure your device in advance</li></ul>
  </div>
  <div class="feature" style="left:667px">
    <div class="feature-head"><svg width="52" height="44" viewBox="0 0 52 44"><path d="M6 14V6h36M46 30v8H10" fill="none" stroke="#fff" stroke-width="5"/><path d="M38 0l10 6-10 6zM14 32L4 38l10 6z" fill="#fff"/></svg>Claim and fix your device</div>
    <ul><li>- Claim your money you have paid</li><li>- Fix your broken devices</li><li>- Fast and reliable</li></ul>
  </div>
</section>

<section class="band" style="top:773px;height:280px">
  <h2 class="section-title" style="top:24px">Customer Raiting</h2>
  <svg class="arrow" style="left:24px;top:150px" width="18" height="34"><path d="M18 0v34L0 17z" fill="#fff"/></svg>
  <svg class="arrow" style="left:1104px;top:150px" width="18" height="34"><path d="M0 0v34l18-17z" fill="#fff"/></svg>
  <div class="rating" style="left:72px"><span class="rating-icon" style="background:#2b2b2b"></span><div><div class="rating-name">Orchard Store</div><div class="rating-desc">some info came here with description.</div><div class="stars"><svg width="150" height="24"><g fill="var(--star-red)"><path id="s" d="M12 0l3.5 8 8.5.7-6.5 5.6 2 8.4L12 18l-7.5 4.7 2-8.4L0 8.7 8.5 8z"/><use href="#s" x="31"/><use href="#s" x="62"/><use href="#s" x="93"/><use href="#s" x="124"/></g></svg></div></div></div>
  <div class="rating" style="left:424px"><span class="rating-icon" style="background:#1c1c1c;border:2px dashed #fff"></span><div><div class="rating-name">Riverly Store</div><div class="rating-desc">some info came here with description.</div><div class="stars"><svg width="150" height="24"><g fill="var(--star-blue)"><use href="#s"/><use href="#s" x="31"/><use href="#s" x="62"/><use href="#s" x="93"/><use href="#s" x="124"/></g></svg></div></div></div>
  <div class="rating" style="left:784px"><span class="rating-icon" style="background:#dd3a2b"></span><div><div class="rating-name">Searchly Store</div><div class="rating-desc">some info came here with description.</div><div class="stars"><svg width="150" height="24"><g fill="var(--star-green)"><use href="#s"/><use href="#s" x="31"/><use href="#s" x="62"/><use href="#s" x="93"/><use href="#s" x="124"/></g></svg></div></div></div>
</section>

<section>
  <h2 class="section-title light-title" style="top:1092px">Industry News</h2>
  <article class="card" style="left:114px;top:1156px"><div class="card-img" role="img" aria-label="Customer shopping for a laptop in an electronics store" style="background:linear-gradient(135deg,#5f86b0,#c7d2dc)"></div><h3 class="card-title">Lorem ipsum nipsum saye</h3><div class="card-meta">Posted on: Sep 29th, 2014</div><hr class="card-rule"><p class="card-text">Lorem ipsum nipsum saye Lorem ipsum nipsum saye. Lorem ipsum nipsum saye Lorem ipsum nipsum saye.</p></article>
  <article class="card" style="left:440px;top:1156px"><div class="card-img" role="img" aria-label="Person touching a digital interface screen" style="background:linear-gradient(135deg,#dfe8ee,#b57a62)"></div><h3 class="card-title">Lorem ipsum nipsum saye</h3><div class="card-meta">Posted on: Sep 29th, 2014</div><hr class="card-rule"><p class="card-text">Lorem ipsum nipsum saye Lorem ipsum nipsum saye. Lorem ipsum nipsum saye Lorem ipsum nipsum saye.</p></article>
  <article class="card" style="left:768px;top:1156px"><div class="card-img" role="img" aria-label="Couple browsing televisions on a store wall" style="background:linear-gradient(135deg,#3e6d9a,#c9b8a0)"></div><h3 class="card-title">Lorem ipsum nipsum saye</h3><div class="card-meta">Posted on: Sep 29th, 2014</div><hr class="card-rule"><p class="card-text">Lorem ipsum nipsum saye Lorem ipsum nipsum saye. Lorem ipsum nipsum saye Lorem ipsum nipsum saye.</p></article>
</section>

<section class="band" style="top:1612px;height:348px">
  <h2 class="section-title" style="top:38px">Customer Testimonials</h2>
  <svg class="arrow" style="left:46px;top:184px" width="18" height="34"><path d="M18 0v34L0 17z" fill="#fff"/></svg>
  <svg class="arrow" style="left:1128px;top:184px" width="18" height="34"><path d="M0 0v34l18-17z" fill="#fff"/></svg>
  <div class="video" style="left:88px" role="img" aria-label="Video testimonial thumbnail with presenter"><svg class="play" width="56" height="56"><circle cx="28" cy="28" r="28" fill="#7cc42a"/><path d="M21 15l20 13-20 13z" fill="#fff"/></svg></div>
  <div class="video" style="left:431px" role="img" aria-label="Video testimonial thumbnail with presenter"><svg class="play" width="56" height="56"><circle cx="28" cy="28" r="28" fill="#7cc42a"/><path d="M21 15l20 13-20 13z" fill="#fff"/></svg></div>
  <div class="video" style="left:773px" role="img" aria-label="Video testimonial thumbnail with presenter"><svg class="play" width="56" height="56"><circle cx="28" cy="28" r="28" fill="#7cc42a"/><path d="M21 15l20 13-20 13z" fill="#fff"/></svg></div>
</section>

<section>
  <h2 class="section-title light-title" style="top:2011px">Welcome to our Blog</h2>
  <article class="card" style="left:114px;top:2085px"><div class="card-img" role="img" aria-label="Technician repairing electronics at a workbench" style="background:linear-gradient(135deg,#2d3b5a,#9aa3ad)"></div><h3 class="card-title">Lorem ipsum nipsum saye</h3><div class="blog-meta">Sep 29th, 2014 / 10 Comments</div></article>
  <article class="card" style="left:440px;top:2085px"><div class="card-img" role="img" aria-label="Hands typing on a laptop holding a payment card" style="background:linear-gradient(135deg,#e8e8e6,#b9b4ad)"></div><h3 class="card-title">Lorem ipsum nipsum saye</h3><div class="blog-meta">Sep 29th, 2014 / 10 Comments</div></article>
  <article class="card" style="left:768px;top:2085px"><div class="card-img" role="img" aria-label="Person holding two pens against a light blue backdrop" style="background:linear-gradient(135deg,#b9d6e6,#e2b89a)"></div><h3 class="card-title">Lorem ipsum nipsum saye</h3><div class="blog-meta">Sep 29th, 2014 / 10 Comments</div></article>
</section>

<footer class="site-footer">
  <h4 class="footer-heading" style="left:94px;width:234px">WELCOME TO BH</h4>
  <div class="footer-links" style="left:98px"><span>Our Plans</span><span>Blog</span><span>Benefits</span><span>News</span><span>About us</span><span>Support</span><span>Contact us</span><span>Terms</span></div>
  <h4 class="footer-heading" style="left:424px;width:170px;border:0">SOCIAL MEDIA FEED</h4>
  <div class="social-squares"><span></span><span style="background:#3fa9e0"></span><span style="background:#c9302c"></span></div>
  <div class="feed">
    <div class="feed-item"><span class="feed-dot"></span><div><div class="feed-name">Name of person</div><div class="feed-text">This is an example of a social feed post.</div></div></div>
    <div class="feed-item"><span class="feed-dot"></span><div><div class="feed-name">Name of person</div><div class="feed-text">This is an example of a social feed post.</div></div></div>
    <div class="feed-item"><span class="feed-dot"></span><div><div class="feed-name">Name of person</div><div class="feed-text">This is an example of a social feed post.</div></div></div>
  </div>
  <h4 class="footer-heading" style="left:824px;width:234px">CONTACT US</h4>
  <div class="contact">
    <div><svg width="14" height="14"><circle cx="7" cy="7" r="6" fill="#fff"/></svg>48 Lantern Lane</div>
    <div style="padding-left:22px">Harborview 1029</div>
    <div><svg width="14" height="14"><rect x="3" y="1" width="8" height="12" rx="1" fill="#fff"/></svg>Ph: (555) 014-2290</div>
    <div><svg width="14" height="14"><rect x="1" y="3" width="12" height="9" fill="#fff"/><path d="M1 3l6 5 6-5" stroke="#3a2d23" fill="none"/></svg>Email: hello@brightharbor.example</div>
  </div>
</footer>
<div class="copyright">Copyright © 2014 Bright Harbor Assurance</div>

</body>
</html>
```